Business Card Design Project

Doctor, Pain Management. Need a new business card design with appointment info on the back. New address is 18 Corvell Road, Suite 304, Brisdale, NJ 07391. Right now I believe the rest of the information is staying the same.

```html
<!DOCTYPE html>
<html lang="en">
<head>
<meta charset="utf-8">
<title>Restful Pain Management – Business Card</title>
<link rel="stylesheet" href="https://fonts.googleapis.com/css2?family=Libre+Baskerville:wght@400;700&display=swap">
<style>
  :root {
    --page: #e4e4e2;
    --card: #f4f4f3;
    --ink: #111111;
    --band-black: #0c0c0c;
    --olive: #3b3a26;
    --olive-light: #4a4830;
    --gold: #f0e98a;
    --lime: #e8e23a;
    --rule: #2a2a22;
  }
  * { box-sizing: border-box; margin: 0; padding: 0; }
  html, body { width: 1200px; height: 864px; overflow: hidden; }
  body {
    background: var(--page);
    font-family: "Libre Baskerville", Georgia, serif;
    color: var(--ink);
    position: relative;
  }
  .card {
    position: absolute;
    top: 278px;
    width: 540px;
    height: 309px;
    background: var(--card);
    overflow: hidden;
    box-shadow: 0 6px 18px rgba(0,0,0,0.18);
  }
  /* ---------- front ---------- */
  .card--front { left: 40px; }
  .front-band {
    position: absolute; left: 0; top: 0; width: 100%; height: 118px;
    background: var(--band-black);
  }
  .spine-art {
    position: absolute; left: 40px; top: 0; width: 120px; height: 118px;
    background: radial-gradient(ellipse at 55% 50%, #c2461c 0%, #6a2a1c 35%, #2a1a18 70%, var(--band-black) 100%);
  }
  .clinic-name {
    position: absolute; left: 112px; top: 66px;
    font-size: 27px; font-weight: 700; color: var(--gold); letter-spacing: 0.2px;
    white-space: nowrap;
  }
  .neck-photo {
    position: absolute; right: 0; bottom: 0; width: 220px; height: 130px;
    background: radial-gradient(ellipse at 70% 60%, #c9a692 0%, #dcc3b4 45%, rgba(244,244,243,0) 80%);
  }
  .contacts { position: absolute; left: 18px; top: 136px; list-style: none; }
  .contacts li {
    display: flex; align-items: center; gap: 8px;
    font-size: 14px; line-height: 24px; white-space: nowrap;
  }
  .contacts svg { width: 16px; height: 16px; flex: none; }
  .address {
    position: absolute; left: 18px; top: 262px; font-size: 14px; white-space: nowrap;
    position: absolute; z-index: 1;
  }
  .doctor { position: absolute; right: 22px; top: 150px; text-align: right; }
  .doctor-name { font-size: 19px; font-weight: 700; }
  .doctor-title { font-size: 13px; margin-top: 2px; }

  /* ---------- back ---------- */
  .card--back { left: 620px; }
  .heading-row {
    position: absolute; left: 0; top: 24px; width: 100%; height: 34px;
    display: flex; align-items: center; justify-content: center; gap: 14px;
  }
  .heading-rule { width: 120px; height: 4px; background: var(--rule); }
  .heading-tag {
    background: var(--olive); color: #f4f4f3; font-size: 21px;
    padding: 4px 18px; border-radius: 3px;
  }
  .notice {
    position: absolute; left: 0; top: 68px; width: 100%;
    text-align: center; font-size: 13px; line-height: 18px;
  }
  .field {
    position: absolute; left: 22px; font-size: 13px; display: flex; align-items: flex-end; gap: 6px;
  }
  .field .line { border-bottom: 1px solid var(--ink); height: 14px; }
  .field--for { top: 118px; width: 496px; }
  .field--for .line { flex: 1; }
  .field--date { top: 144px; width: 290px; }
  .field--date .line { flex: 1; }
  .field--time { top: 144px; left: 320px; width: 198px; }
  .field--time .line { flex: 1; }
  .days {
    position: absolute; left: 22px; top: 172px; width: 496px;
    display: flex; justify-content: space-between; font-size: 14px; list-style: none;
  }
  .days li { display: flex; align-items: center; gap: 4px; }
  .days .box { width: 12px; height: 12px; border: 1px solid var(--ink); background: #fff; }
  .back-band {
    position: absolute; left: 0; bottom: 0; width: 100%; height: 100px;
    background: linear-gradient(180deg, var(--olive-light), var(--olive));
  }
  .band-phones {
    position: absolute; left: 22px; top: 14px; font-size: 12px; line-height: 19px; color: var(--lime);
  }
  .band-web {
    position: absolute; right: 22px; bottom: 14px; text-align: right;
    font-size: 12px; line-height: 19px; color: var(--lime);
  }
</style>
</head>
<body>

<section class="card card--front" aria-label="Business card front">
  <div class="front-band"></div>
  <div class="spine-art" role="img" aria-label="Illustration of a human back with the spine glowing red"></div>
  <h1 class="clinic-name">Restful Pain Management</h1>
  <div class="neck-photo" role="img" aria-label="Photo of a woman holding the back of her neck"></div>

  <ul class="contacts">
    <li>
      <svg viewBox="0 0 16 16" aria-hidden="true"><rect width="16" height="16" fill="#111"/><path d="M5 3.5c-.8.6-1 1.6-.5 2.8 1 2.4 2.8 4.3 5.2 5.3 1.2.5 2.2.3 2.8-.5l-1.6-1.6-1.3.8c-1.3-.6-2.4-1.7-3-3l.8-1.3z" fill="#fff"/></svg>
      (973) 555-0148
    </li>
    <li>
      <svg viewBox="0 0 16 16" aria-hidden="true"><rect width="16" height="16" fill="#111"/><rect x="3" y="6" width="10" height="7" fill="#fff"/><rect x="5" y="3" width="6" height="4" fill="none" stroke="#fff"/></svg>
      (973) 555.0162
    </li>
    <li>
      <svg viewBox="0 0 16 16" aria-hidden="true"><rect width="16" height="16" fill="#111"/><rect x="3" y="4.5" width="10" height="7" fill="none" stroke="#fff"/><path d="M3 4.5l5 4 5-4" fill="none" stroke="#fff"/></svg>
      restfulpmc.service@mailhub.net
    </li>
    <li>
      <svg viewBox="0 0 16 16" aria-hidden="true"><rect width="16" height="16" fill="#111"/><circle cx="8" cy="8" r="5" fill="none" stroke="#fff"/><ellipse cx="8" cy="8" rx="2.2" ry="5" fill="none" stroke="#fff"/><path d="M3 8h10" stroke="#fff"/></svg>
      www.restfulpm.com
    </li>
  </ul>

  <div class="doctor">
    <p class="doctor-name">Dr. Weiran Lao</p>
    <p class="doctor-title">M.D., Ph.D.</p>
  </div>

  <p class="address">18 Corvell Road, Suite 304, Brisdale, NJ 07391</p>
</section>

<section class="card card--back" aria-label="Appointment card back">
  <div class="heading-row">
    <span class="heading-rule"></span>
    <h2 class="heading-tag">Appoinment</h2>
    <span class="heading-rule"></span>
  </div>
  <p class="notice">If you are unable to keep your appoinment,<br>please contact us as soon as posible.</p>

  <div class="field field--for"><span>For:</span><span class="line"></span></div>
  <div class="field field--date"><span>Date:</span><span class="line"></span></div>
  <div class="field field--time"><span>Time:</span><span class="line"></span></div>

  <ul class="days">
    <li><span class="box"></span>Mon</li>
    <li><span class="box"></span>Tue</li>
    <li><span class="box"></span>Wed</li>
    <li><span class="box"></span>Thu</li>
    <li><span class="box"></span>Fri</li>
    <li><span class="box"></span>Sat</li>
    <li><span class="box"></span>Sun</li>
  </ul>

  <div class="back-band">
    <p class="band-phones">(973) 555-0148<br>(973) 555.0162</p>
    <p class="band-web">www.restfulpm.com<br>restfulpmc.service@mailhub.net</p>
  </div>
</section>

</body>
</html>
```